Business card design for holistic health care clinic

We need a double-sided business card design for our holistic health care clinic that integrates our logo design and also its color scheme. My business is called Valmira. It is an integrative medicine clinic. You have already done the logo for me. Please ensure an elegant and upscale design that is not cluttered, but still has all the necessary information (please see below for details).

Target Market(s)

Wellness, fitness, rehabilitation for educated, well-traveled open-minded clients who are focused on natural, organic, balanced and preventive healthcare and lifestyle.

Industry/Entity Type

Medical

Contact Information for Business Card

Modern, clean.

Number of Pages Required

1 page

Font styles to use
Serif
Sans Serif

Colors

Designer to choose colors to be used in the design.

Requirements
Must have
• Logo on one side, all other information on the other side.
• Other information should include:
• Tobias Wrenfeld - DOE, CPT, LMT
• 4100 East Marrow Drive
• Austin, TX 78119
• 512 555 0148
• 818 555 0192
• info@ValmiraHealth.example
• t.wrenfeld@ValmiraHealth.example
Nice to have
• Darker background on front - but not totally black - shaded/dark gray.

```html
<!DOCTYPE html>
<html lang="en">
<head>
<meta charset="utf-8">
<title>Valmira Business Card</title>
<link href="https://fonts.googleapis.com/css2?family=Roboto:wght@400;500;700&family=Roboto+Condensed:wght@500;700&display=swap" rel="stylesheet">
<style>
  :root {
    --backdrop: #5a4636;
    --card: #2a2a2a;
    --card-edge: #232323;
    --brand-blue: #0a8fc7;
    --text-light: #ececec;
  }
  * { margin: 0; padding: 0; box-sizing: border-box; }
  html, body { width: 1200px; height: 960px; overflow: hidden; }
  body {
    background: var(--backdrop);
    position: relative;
    font-family: "Roboto", Arial, sans-serif;
  }
  .card {
    position: absolute;
    width: 600px;
    height: 342px;
    border-radius: 20px;
    background: linear-gradient(160deg, #2e2e2e 0%, var(--card) 55%, var(--card-edge) 100%);
    overflow: hidden;
    box-shadow: 0 4px 8px rgba(0,0,0,0.35);
  }
  .card--front { left: 314px; top: 113px; }
  .card--back { left: 311px; top: 472px; }

  .front__tab {
    position: absolute; left: 0; top: 51px;
    width: 12px; height: 29px; background: var(--brand-blue);
  }
  .front__band {
    position: absolute; left: 0; right: 0; bottom: 0;
    height: 13px; background: var(--brand-blue);
  }
  .holder {
    position: absolute; left: 46px; top: 55px;
    font-family: "Roboto Condensed", Arial, sans-serif;
    color: var(--brand-blue);
    white-space: nowrap;
  }
  .holder__name { font-size: 22px; font-weight: 700; letter-spacing: 0.2px; }
  .holder__credentials { font-size: 13px; font-weight: 700; margin-left: 3px; }

  .address {
    position: absolute; left: 46px; top: 174px;
    color: var(--text-light); font-size: 14px; line-height: 18px;
  }
  .contacts {
    position: absolute; left: 46px; top: 220px;
    list-style: none; color: var(--text-light); font-size: 14px;
  }
  .contacts li { display: flex; align-items: center; height: 19.5px; }
  .contacts svg { width: 13px; height: 13px; margin-right: 10px; fill: var(--brand-blue); flex: none; }

  .wordmark {
    position: absolute;
    font-family: "Roboto", Arial, sans-serif;
    font-weight: 700;
    color: var(--brand-blue);
    display: flex; align-items: center; gap: 10px;
    white-space: nowrap;
  }
  .wordmark__dot { border-radius: 50%; background: var(--brand-blue); flex: none; }
  .wordmark--front { left: 326px; top: 222px; font-size: 44px; }
  .wordmark--front .wordmark__dot { width: 14px; height: 14px; }
  .wordmark--back { left: 0; right: 0; top: 140px; justify-content: center; font-size: 58px; }
  .wordmark--back .wordmark__dot { width: 18px; height: 18px; }

  .tagline {
    position: absolute; left: 0; right: 0; top: 282px;
    text-align: center; color: var(--text-light); font-size: 14.5px;
  }
</style>
</head>
<body>
  <section class="card card--front">
    <div class="front__tab"></div>
    <p class="holder"><span class="holder__name">TOBIAS WRENFELD</span><span class="holder__credentials">- DOE, CPT, LMT</span></p>
    <address class="address" style="font-style:normal">4100 East Marrow Drive<br>Austin, TX 78119</address>
    <ul class="contacts">
      <li><svg viewBox="0 0 24 24"><path d="M6.6 10.8a15.1 15.1 0 0 0 6.6 6.6l2.2-2.2a1 1 0 0 1 1-.25 11.4 11.4 0 0 0 3.6.57 1 1 0 0 1 1 1V20a1 1 0 0 1-1 1A17 17 0 0 1 3 4a1 1 0 0 1 1-1h3.5a1 1 0 0 1 1 1c0 1.25.2 2.45.57 3.57a1 1 0 0 1-.25 1z"/></svg>512 555 0148</li>
      <li><svg viewBox="0 0 24 24"><path d="M7 1h10a2 2 0 0 1 2 2v18a2 2 0 0 1-2 2H7a2 2 0 0 1-2-2V3a2 2 0 0 1 2-2zm0 3v14h10V4zm5 15.5a1.2 1.2 0 1 0 0 2.4 1.2 1.2 0 0 0 0-2.4z"/></svg>818 555 0192</li>
      <li><svg viewBox="0 0 24 24"><path d="M2 5h20v14H2zm2 2v.5l8 5 8-5V7l-8 5z"/></svg>t.wrenfeld@ValmiraHealth.example</li>
      <li><svg viewBox="0 0 24 24"><path d="M12 2a10 10 0 1 0 0 20 10 10 0 0 0 0-20zm-1 17.9A8 8 0 0 1 4.2 10.6L9 15v1a2 2 0 0 0 2 2zm6.9-2.5A2 2 0 0 0 16 16h-1v-3a1 1 0 0 0-1-1H8v-2h2a1 1 0 0 0 1-1V7h2a2 2 0 0 0 2-2v-.4a8 8 0 0 1 2.9 12.8z"/></svg>www.ValmiraHealth.example</li>
    </ul>
    <div class="wordmark wordmark--front"><span class="wordmark__dot"></span>VALMIRA</div>
    <div class="front__band"></div>
  </section>

  <section class="card card--back">
    <div class="wordmark wordmark--back"><span class="wordmark__dot"></span>VALMIRA</div>
    <p class="tagline">it’s all about you – your health, your objectives</p>
  </section>
</body>
</html>
```